Tidewell Comforts, a portable luxury restroom trailer company needs a landing page

We need a landing page for a luxury portable restroom trailer company. This should be modern, and simple - use any combination of Pantone colors: Warm Gray 1C, Black 7C, 7529c, 873C, 8003C

We rent these trailers for special events like weddings, private parties, festivals, family reunions, team building, wine tastings, beer tastings, food truck round-ups, etc.

An idea of the landing page is in the files below. Please use stock photography and placeholder text for now. The winning design will be given final content.

Requirements
Must have
• Multiple "Get Quote" buttons or a place for them to type in type of rental, how many people etc

```html
<!DOCTYPE html>
<html lang="en">
<head>
<meta charset="utf-8">
<title>Tidewell Comforts – Luxury Portable Restroom Trailers</title>
<link href="https://fonts.googleapis.com/css2?family=Oswald:wght@500;600&family=Lato:wght@400;700;900&display=swap" rel="stylesheet">
<style>
:root{
  --brand:#2467b2;
  --brand-deep:#1b4f9c;
  --brand-light:#d7e4f1;
  --ink:#222;
  --text:#555;
  --muted:#8a8a8a;
  --line:#e3e6ea;
  --white:#fff;
  --footer:#2b2b2b;
}
*{box-sizing:border-box;margin:0;padding:0}
html,body{width:1200px;height:3762px;overflow:hidden}
body{position:relative;font-family:"Lato",sans-serif;color:var(--text);background:var(--white)}
.abs{position:absolute}
.display{font-family:"Oswald",sans-serif;font-weight:600;text-transform:uppercase;letter-spacing:-.5px}

/* top bar */
.topbar{left:0;top:0;width:1200px;height:44px;border-bottom:1px solid var(--line);font-size:13px;color:#444}
.topbar .contact{left:143px;top:13px;display:flex;align-items:center;gap:6px}
.topbar .account{left:798px;top:13px;display:flex;align-items:center;gap:6px}
.topbar svg{width:12px;height:12px;fill:var(--brand)}
.topbar .social{left:956px;top:12px;display:flex;gap:9px}
.social-btn{border-radius:50%;display:flex;align-items:center;justify-content:center}
.social-btn svg{fill:none;stroke-width:2}
.topbar .social-btn{width:18px;height:18px;border:1.5px solid #777}
.topbar .social-btn svg{width:9px;height:9px;stroke:#777}

/* header */
.logo{left:143px;top:52px;display:flex;align-items:center;gap:10px}
.logo .mark{width:40px;height:68px;background:var(--brand);border-radius:3px}
.logo .name{font-family:"Oswald",sans-serif;font-weight:600;font-size:31px;color:var(--brand);text-transform:uppercase}
.nav{top:76px;left:0;width:1200px;font-size:14px;color:#333}
.nav a{position:absolute;text-decoration:none;color:inherit}
.nav a.active{color:var(--brand)}
.nav a.active::after{content:"";position:absolute;left:-2px;right:-2px;top:27px;height:3px;background:var(--brand)}

/* hero */
.hero{left:0;top:131px;width:1200px;height:533px;background:linear-gradient(180deg,#fff 0%,#b9d1ea 30%,#5b90c9 62%,#2a68b0 100%)}
.hero-title{left:143px;top:222px;font-size:58px;line-height:63px;color:#fff;text-shadow:0 2px 4px rgba(0,0,0,.35)}
.btn-ghost{border:2px solid #fff;color:#fff;border-radius:40px;font-weight:900;font-size:16px;display:flex;align-items:center;justify-content:center;text-transform:uppercase}
.hero-cta{left:143px;top:460px;width:210px;height:77px}
.dots{left:144px;top:613px;display:flex;gap:8px}
.dots span{width:10px;height:10px;border-radius:50%;background:#fff}
.dots span.off{background:transparent;border:2px solid #fff}
.collage{left:0;top:0;width:1200px;height:800px;z-index:3;pointer-events:none}

/* events */
.events{left:0;top:664px;width:1200px;height:740px;background:linear-gradient(180deg,#dbe3ec 0%,#c9d4df 50%,#b3c2cf 100%)}
.events-bg{left:0;top:0;width:1200px;height:740px;background:linear-gradient(90deg,rgba(255,255,255,.55),rgba(255,255,255,.25),rgba(255,255,255,.55))}
.section-title{left:0;width:1200px;text-align:center;color:var(--brand);font-size:50px}
.card{top:850px;width:295px;height:442px;background:#fff;box-shadow:0 6px 18px rgba(0,0,0,.18)}
.card .photo{left:0;top:0;width:295px;height:187px}
.card .date{left:2px;top:113px;width:80px;height:71px;background:rgba(30,30,30,.55);color:#fff;font-weight:900;font-size:21px;line-height:25px;text-align:center;padding-top:10px}
.card .thumb{left:188px;top:135px;width:88px;height:88px;border-radius:50%;border:4px solid #fff;background:linear-gradient(160deg,#8fa3b5,#48607a)}
.card h3{left:26px;top:213px;font-size:17px;font-weight:900;color:var(--brand);text-transform:uppercase}
.card .loc{left:26px;top:250px;font-size:12px;color:#777}
.card .loc b{color:#222}
.card .loc svg{width:9px;height:11px;fill:var(--brand);vertical-align:-1px;margin:0 3px}
.card p{left:26px;top:282px;width:245px;font-size:13px;line-height:22px;color:#666}
.btn-outline{border:2px solid var(--brand);color:var(--brand);border-radius:40px;font-weight:900;font-size:15px;display:flex;align-items:center;justify-content:center;text-transform:uppercase;background:#fff}
.card .btn-outline{left:25px;top:365px;width:139px;height:53px;font-size:14px}
.round-arrow{width:44px;height:44px;border-radius:50%;border:2px solid #888;background:rgba(255,255,255,.6);display:flex;align-items:center;justify-content:center}
.round-arrow svg{width:14px;height:14px;stroke:#555;stroke-width:2.2;fill:none}

/* products */
.product{left:143px;width:914px;height:373px;border:3px solid var(--brand-light);border-radius:187px;background:#fff}
.product .photo{width:324px;height:324px;border-radius:50%;top:21px}
.product h3{font-size:28px;font-weight:900;color:#222;text-transform:uppercase;letter-spacing:-.3px}
.product p{font-size:13.5px;line-height:24.8px;color:#666;width:470px}
.product .btn-outline{width:159px;height:62px;font-size:16px}

/* contact */
.quote{left:0;top:2974px;width:1200px;height:610px;background:linear-gradient(180deg,#2a5fb8 0%,#1e56b6 45%,#1848a3 100%)}
.field{width:295px;height:56px;background:#fff;font-size:14px;color:#444;display:flex;align-items:center;justify-content:space-between;padding:0 14px 0 31px}
.field svg{width:11px;height:11px;fill:#999}
.quote-submit{left:496px;top:3416px;width:210px;height:76px}

/* footer */
.footer{left:0;top:3584px;width:1200px;height:178px;background:var(--footer)}
.finfo{display:flex;align-items:center;gap:18px;font-size:13px;line-height:25px;color:#fff}
.finfo .ico{width:44px;height:44px;border-radius:50%;border:2px solid #fff;display:flex;align-items:center;justify-content:center;flex:none}
.finfo .ico.fill{background:var(--brand);border-color:var(--brand)}
.finfo svg{width:16px;height:16px;fill:#fff}
.copy{left:143px;top:3723px;font-size:11.5px;color:#fff}
.fsocial{left:930px;top:3717px;display:flex;gap:6px}
.fsocial .social-btn{width:28px;height:28px;border:1.5px solid #fff}
.fsocial .social-btn svg{width:12px;height:12px;stroke:#fff}
</style>
</head>
<body>

<div class="abs topbar">
  <div class="abs contact">
    <svg viewBox="0 0 24 24"><path d="M6.6 10.8a15.1 15.1 0 006.6 6.6l2.2-2.2a1 1 0 011-.25 11.4 11.4 0 003.6.6 1 1 0 011 1V20a1 1 0 01-1 1A17 17 0 013 4a1 1 0 011-1h3.5a1 1 0 011 1 11.4 11.4 0 00.6 3.6 1 1 0 01-.25 1z"/></svg>
    <span>+1 555 014 2290</span><span>&nbsp;|&nbsp;</span>
    <svg viewBox="0 0 24 24"><path d="M2 5h20v14H2zm2 2v.5l8 5 8-5V7z"/></svg>
    <span>info@tidewellcomforts.com</span>
  </div>
  <div class="abs account">
    <svg viewBox="0 0 24 24"><circle cx="12" cy="7" r="5"/><path d="M2 22c0-6 4.5-9 10-9s10 3 10 9z"/></svg>
    <span>Login</span><span>&nbsp;|&nbsp;</span>
    <svg viewBox="0 0 24 24"><path d="M10 4h10v16H10v-3h8V7h-8zM2 11h9V7l6 5-6 5v-4H2z"/></svg>
    <span>Sign Up</span>
  </div>
  <div class="abs social">
    <span class="social-btn"><svg viewBox="0 0 12 12"><path d="M3 6h6M6 3l3 3-3 3"/></svg></span>
    <span class="social-btn"><svg viewBox="0 0 12 12"><path d="M3 6h6M6 3l3 3-3 3"/></svg></span>
    <span class="social-btn"><svg viewBox="0 0 12 12"><path d="M3 6h6M6 3l3 3-3 3"/></svg></span>
    <span class="social-btn"><svg viewBox="0 0 12 12"><path d="M3 6h6M6 3l3 3-3 3"/></svg></span>
  </div>
</div>

<div class="abs logo"><div class="mark"></div><div class="name">Tidewell Comforts</div></div>
<nav class="abs nav">
  <a class="active" style="left:707px">HOME</a>
  <a style="left:787px">EVENTS</a>
  <a style="left:876px">PRODUCTS</a>
  <a style="left:990px">CONTACT</a>
</nav>

<section class="abs hero"></section>
<h1 class="abs display hero-title">Providing quality<br>and luxury portable<br>restroom trailers</h1>
<div class="abs btn-ghost hero-cta">Get Started</div>
<div class="abs dots"><span></span><span class="off"></span><span></span></div>

<svg class="abs collage" viewBox="0 0 1200 800" role="img" aria-label="Diamond collage of portable restroom units and restroom trailers at outdoor sites">
  <g transform="translate(876 453) rotate(45)">
    <rect x="-218" y="-218" width="140" height="140" fill="#6f9fcf"/>
    <rect x="-70" y="-218" width="140" height="140" fill="#2f6fd0"/>
    <rect x="78" y="-218" width="140" height="140" fill="#5d7d55"/>
    <rect x="-218" y="-70" width="140" height="140" fill="#4f7db8"/>
    <rect x="-70" y="-70" width="140" height="140" fill="#3d7fd6"/>
    <rect x="78" y="-70" width="140" height="140" fill="#6f6f6f"/>
    <rect x="-218" y="78" width="140" height="140" fill="#6b7a4f"/>
    <rect x="-70" y="78" width="140" height="140" fill="#3e9ac2"/>
    <rect x="78" y="78" width="140" height="140" fill="#eef1f4" stroke="#fff" stroke-width="6"/>
  </g>
</svg>

<section class="abs events" role="img" aria-label="Faded photo of a row of portable restrooms at an outdoor event">
  <div class="abs events-bg"></div>
</section>
<h2 class="abs display section-title" style="top:755px">Events</h2>

<div class="abs round-arrow" style="left:73px;top:1083px"><svg viewBox="0 0 14 14"><path d="M9 2L4 7l5 5"/></svg></div>
<div class="abs round-arrow" style="left:1083px;top:1083px"><svg viewBox="0 0 14 14"><path d="M5 2l5 5-5 5"/></svg></div>

<article class="abs card" style="left:143px">
  <div class="abs photo" role="img" aria-label="Wedding couple celebrating" style="background:linear-gradient(135deg,#d9d2c8,#8d8375 60%,#5b5148)"></div>
  <div class="abs date">JAN<br>31</div>
  <div class="abs thumb" role="img" aria-label="Restroom trailer"></div>
  <h3 class="abs">Weddings</h3>
  <div class="abs loc"><b>Location :</b><svg viewBox="0 0 10 12"><path d="M5 0a4 4 0 00-4 4c0 3 4 8 4 8s4-5 4-8a4 4 0 00-4-4zm0 5.5A1.5 1.5 0 115 2.5a1.5 1.5 0 010 3z"/></svg>23, aliquip eommodo</div>
  <p class="abs">Lorem ipsum dolor sit aonsectetur adipiscing elit, sed do eiusmod tempor incididunt ut labore et dolore</p>
  <div class="abs btn-outline">Read More</div>
</article>

<article class="abs card" style="left:453px">
  <div class="abs photo" role="img" aria-label="Friends toasting at a private party" style="background:linear-gradient(135deg,#b23a7a,#6a2a4e 55%,#2b1c24)"></div>
  <div class="abs date">JAN<br>31</div>
  <div class="abs thumb" role="img" aria-label="Blue portable restroom" style="background:linear-gradient(160deg,#6f9ddb,#2456a8)"></div>
  <h3 class="abs">Private Parties</h3>
  <div class="abs loc"><b>Location :</b><svg viewBox="0 0 10 12"><path d="M5 0a4 4 0 00-4 4c0 3 4 8 4 8s4-5 4-8a4 4 0 00-4-4zm0 5.5A1.5 1.5 0 115 2.5a1.5 1.5 0 010 3z"/></svg>23, aliquip eommodo</div>
  <p class="abs">Lorem ipsum dolor sit aonsectetur adipiscing elit, sed do eiusmod tempor incididunt ut labore et dolore</p>
  <div class="abs btn-outline">Read More</div>
</article>

<article class="abs card" style="left:761px">
  <div class="abs photo" role="img" aria-label="Festival crowd under fireworks" style="background:linear-gradient(180deg,#2a2530,#6b4a3f 60%,#1e1a1c)"></div>
  <div class="abs date">JAN<br>31</div>
  <div class="abs thumb" role="img" aria-label="Row of blue portable restrooms" style="background:linear-gradient(180deg,#8fc0d8,#1f7fc9)"></div>
  <h3 class="abs">Festivals</h3>
  <div class="abs loc"><b>Location :</b><svg viewBox="0 0 10 12"><path d="M5 0a4 4 0 00-4 4c0 3 4 8 4 8s4-5 4-8a4 4 0 00-4-4zm0 5.5A1.5 1.5 0 115 2.5a1.5 1.5 0 010 3z"/></svg>23, aliquip eommodo</div>
  <p class="abs">Lorem ipsum dolor sit aonsectetur adipiscing elit, sed do eiusmod tempor incididunt ut labore et dolore</p>
  <div class="abs btn-outline">Read More</div>
</article>

<h2 class="abs display section-title" style="top:1500px">Featured Products</h2>

<article class="abs product" style="top:1632px">
  <div class="abs photo" role="img" aria-label="Blue portable restroom unit on pavement" style="left:23px;background:linear-gradient(150deg,#c9ccd1,#3f82c9 45%,#5b6b55)"></div>
  <h3 class="abs" style="left:391px;top:37px">Duis aute irure dolor</h3>
  <p class="abs" style="left:391px;top:88px">Lorem ipsum dolor sit amet, consectetur adipiscing elit, sed do eiusmod tempor incididunt ut labore et dolore magna aliqua. Quis ipsum suspendisse ultrices gravida. Risus commodo viverra maecenas accumsan lacus vel facilisis. Lorem ipsum dolor sit amet, consectetur adipiscing elit, sed do eiusmod tempocididunt ut labore et dolore magna aliqua. Quis ipsum suspendisse ultrices gravida.isus commodo viverra maecenas accumsan lacus vel facilisis.</p>
  <div class="abs btn-outline" style="left:391px;top:266px">Read More</div>
</article>

<article class="abs product" style="top:2041px">
  <div class="abs photo" role="img" aria-label="Silver luxury restroom trailer with steps" style="left:564px;background:linear-gradient(150deg,#2e3a2a,#a9acae 50%,#6d7073)"></div>
  <h3 class="abs" style="right:384px;top:37px;text-align:right">Duis aute irure dolor</h3>
  <p class="abs" style="left:64px;top:88px;text-align:right">Lorem ipsum dolor sit amet, consectetur adipiscing elit, sed do eiusmod tempor incididunt ut labore et dolore magna aliqua. Quis ipsum suspendisse ultrices gravida. Risus commodo viverra maecenas accumsan lacus vel facilisis. Lorem ipsum dolor sit amet, consectetur adipiscing elit, sed do eiusmod tempocididunt ut labore et dolore magna aliqua. Quis ipsum suspendisse ultrices gravida.isus commodo viverra maecenas accumsan lacus vel facilisis.</p>
  <div class="abs btn-outline" style="left:371px;top:267px">Read More</div>
</article>

<article class="abs product" style="top:2451px">
  <div class="abs photo" role="img" aria-label="Long row of grey portable restrooms in a city" style="left:23px;background:linear-gradient(150deg,#8fb4d8,#8a8f94 45%,#5e6266)"></div>
  <h3 class="abs" style="left:391px;top:37px">Duis aute irure dolor</h3>
  <p class="abs" style="left:391px;top:88px">Lorem ipsum dolor sit amet, consectetur adipiscing elit, sed do eiusmod tempor incididunt ut labore et dolore magna aliqua. Quis ipsum suspendisse ultrices gravida. Risus commodo viverra maecenas accumsan lacus vel facilisis. Lorem ipsum dolor sit amet, consectetur adipiscing elit, sed do eiusmod tempocididunt ut labore et dolore magna aliqua. Quis ipsum suspendisse ultrices gravida.isus commodo viverra maecenas accumsan lacus vel facilisis.</p>
  <div class="abs btn-outline" style="left:391px;top:266px">Read More</div>
</article>

<div class="abs round-arrow" style="left:549px;top:2875px"><svg viewBox="0 0 14 14"><path d="M9 2L4 7l5 5"/></svg></div>
<div class="abs round-arrow" style="left:606px;top:2875px"><svg viewBox="0 0 14 14"><path d="M5 2l5 5-5 5"/></svg></div>

<section class="abs quote" role="img" aria-label="Blue-tinted photo of a row of portable restrooms"></section>
<h2 class="abs display section-title" style="top:3052px;color:#fff">Contact us for a quote</h2>

<div class="abs field" style="left:143px;top:3168px">Enter Name<svg viewBox="0 0 24 24"><circle cx="12" cy="7" r="5"/><path d="M2 22c0-6 4.5-9 10-9s10 3 10 9z"/></svg></div>
<div class="abs field" style="left:453px;top:3168px">Email Address<svg viewBox="0 0 24 24"><path d="M2 5h20v14H2zm2 2v.5l8 5 8-5V7z"/></svg></div>
<div class="abs field" style="left:761px;top:3168px">Enter Phone<svg viewBox="0 0 24 24"><path d="M6.6 10.8a15.1 15.1 0 006.6 6.6l2.2-2.2a1 1 0 011-.25 11.4 11.4 0 003.6.6 1 1 0 011 1V20a1 1 0 01-1 1A17 17 0 013 4a1 1 0 011-1h3.5a1 1 0 011 1 11.4 11.4 0 00.6 3.6 1 1 0 01-.25 1z"/></svg></div>

<div class="abs field" style="left:143px;top:3241px">Type of Event?<svg viewBox="0 0 24 24"><path d="M5 9h14l-7 8z"/></svg></div>
<div class="abs field" style="left:453px;top:3241px">How many People<svg viewBox="0 0 24 24"><path d="M5 9h14l-7 8z"/></svg></div>
<div class="abs field" style="left:761px;top:3241px">Type of Product you're interested in?<svg viewBox="0 0 24 24"><path d="M5 9h14l-7 8z"/></svg></div>

<div class="abs field" style="left:143px;top:3314px">When do you need it?<svg viewBox="0 0 24 24"><path d="M3 5h18v16H3zm2 5v9h14v-9zM7 2h2v4H7zm8 0h2v4h-2z"/></svg></div>
<div class="abs field" style="left:453px;top:3314px">For How Long?<svg viewBox="0 0 24 24"><path d="M5 2h14v2h-1c0 4-3 6-4 8 1 2 4 4 4 8h1v2H5v-2h1c0-4 3-6 4-8-1-2-4-4-4-8H5z"/></svg></div>
<div class="abs field" style="left:761px;top:3314px">Where?<svg viewBox="0 0 10 12"><path d="M5 0a4 4 0 00-4 4c0 3 4 8 4 8s4-5 4-8a4 4 0 00-4-4z"/></svg></div>

<div class="abs btn-ghost quote-submit">Submit</div>

<footer class="abs footer"></footer>
<div class="abs finfo" style="left:224px;top:3615px">
  <div class="ico"><svg viewBox="0 0 10 12"><path d="M5 0a4 4 0 00-4 4c0 3 4 8 4 8s4-5 4-8a4 4 0 00-4-4zm0 5.5A1.5 1.5 0 115 2.5a1.5 1.5 0 010 3z"/></svg></div>
  <div>At vero eos et accu<br>samus et iusto odio dimos ducimu</div>
</div>
<div class="abs finfo" style="left:539px;top:3615px">
  <div class="ico fill"><svg viewBox="0 0 24 24"><path d="M6.6 10.8a15.1 15.1 0 006.6 6.6l2.2-2.2a1 1 0 011-.25 11.4 11.4 0 003.6.6 1 1 0 011 1V20a1 1 0 01-1 1A17 17 0 013 4a1 1 0 011-1h3.5a1 1 0 011 1 11.4 11.4 0 00.6 3.6 1 1 0 01-.25 1z"/></svg></div>
  <div style="font-weight:900;font-size:16px">+1 555 014 2290</div>
</div>
<div class="abs finfo" style="left:766px;top:3615px">
  <div class="ico"><svg viewBox="0 0 24 24"><path d="M2 5h20v14H2zm2 2v.5l8 5 8-5V7z"/></svg></div>
  <div style="font-size:14px">info@tidewellcomforts.com</div>
</div>
<div class="abs copy">Copyrights © 2022, Tidewell Comforts. All rights reserved &nbsp;| Privacy Policy &nbsp;| &nbsp;Terms and Use</div>
<div class="abs fsocial">
  <span class="social-btn"><svg viewBox="0 0 12 12"><path d="M3 6h6M6 3l3 3-3 3"/></svg></span>
  <span class="social-btn"><svg viewBox="0 0 12 12"><path d="M3 6h6M6 3l3 3-3 3"/></svg></span>
  <span class="social-btn"><svg viewBox="0 0 12 12"><path d="M3 6h6M6 3l3 3-3 3"/></svg></span>
  <span class="social-btn"><svg viewBox="0 0 12 12"><path d="M3 6h6M6 3l3 3-3 3"/></svg></span>
</div>

</body>
</html>
```